Weightloss company needs Business Card

We want a business card that is clean and professional, yet portrays that we are a friendly, innovative, and versatile program designed to fit the needs of our clients.
I would like there to be 2 sides, one side having an appointment card, and the other side containing the logo and business information. There can be decorations on both sides. The logo is attached.

Target Market(s)

Men and women 40-60

Industry/Entity Type

Business

Contact Information for Business Card

Font styles to use
Sans Serif

Requirements
Must have
• The logo, space for business information
Nice to have
• The colors in the logo
Should not have
• No pictures of people or food

```html
<!DOCTYPE html>
<html lang="en">
<head>
<meta charset="utf-8">
<title>Brightturn Wellness – Business Card</title>
<link href="https://fonts.googleapis.com/css2?family=Source+Sans+3:wght@400;600;700&display=swap" rel="stylesheet">
<style>
  :root {
    --stage: #161616;
    --card: #ffffff;
    --brand-red: #e8102a;
    --ink: #4a4a4a;
    --dots: #333333;
  }
  * { box-sizing: border-box; margin: 0; padding: 0; }
  html, body { width: 1200px; height: 900px; overflow: hidden; }
  body {
    background: var(--stage);
    font-family: "Source Sans 3", "Myriad Pro", Arial, sans-serif;
    position: relative;
  }
  .card {
    position: absolute;
    top: 306px;
    width: 439px;
    height: 271px;
    background: var(--card);
    border-radius: 12px;
  }
  .card--front { left: 149px; }
  .card--back { left: 608px; }

  .brand {
    position: absolute;
    display: flex;
    align-items: center;
    gap: 8px;
    color: var(--brand-red);
    font-weight: 700;
    font-size: 22px;
    line-height: 1;
    white-space: nowrap;
  }
  .brand__dot {
    width: 14px; height: 14px;
    border-radius: 50%;
    background: var(--brand-red);
    flex: none;
  }
  .card--front .brand { left: 26px; top: 122px; }
  .card--back .brand { left: 0; right: 0; top: 50px; justify-content: center; }

  .contact { position: absolute; left: 251px; top: 61px; color: var(--ink); font-size: 13px; line-height: 16px; }
  .contact__name { color: var(--brand-red); font-weight: 600; font-size: 15px; line-height: 17px; }
  .contact__role { margin-bottom: 10px; }
  .contact__address { margin-bottom: 11px; }
  .contact__list { list-style: none; }
  .contact__list li { display: flex; align-items: center; gap: 7px; }
  .contact__list svg { width: 9px; height: 9px; fill: var(--brand-red); flex: none; }

  .appointment__title {
    position: absolute; left: 0; right: 0; top: 126px;
    text-align: center;
    color: var(--brand-red);
    font-weight: 600;
    font-size: 19px;
  }
  .appointment__field {
    position: absolute; left: 78px;
    display: flex; align-items: baseline;
    color: var(--brand-red);
    font-weight: 600;
    font-size: 12px;
  }
  .appointment__field--name { top: 163px; }
  .appointment__field--when { top: 196px; }
  .appointment__blank {
    display: inline-block;
    border-bottom: 2px dotted var(--dots);
    margin-left: 3px;
  }
  .appointment__note {
    position: absolute; left: 0; right: 0; top: 228px;
    text-align: center;
    color: var(--brand-red);
    font-weight: 600;
    font-size: 12px;
  }
</style>
</head>
<body>
  <section class="card card--front">
    <div class="brand"><span class="brand__dot"></span>Brightturn Wellness</div>
    <div class="contact">
      <p class="contact__name">Daniel Hartley</p>
      <p class="contact__role">Managing Director</p>
      <p class="contact__address">12345, Address Goes Here<br>Country Name, 123456.</p>
      <ul class="contact__list">
        <li><svg viewBox="0 0 10 10"><path d="M2 0.5 L3.6 2.6 L2.8 3.6 Q4 6 6.4 7.2 L7.4 6.4 L9.5 8 L8.3 9.5 Q3.5 9 0.5 1.7 Z"/></svg>044-555 201 734</li>
        <li><svg viewBox="0 0 10 10"><path d="M0.5 2 H9.5 V8 H0.5 Z M0.5 2 L5 5.5 L9.5 2" stroke="#fff" stroke-width="0.8"/></svg>info@brightturn.com</li>
        <li><svg viewBox="0 0 10 10"><circle cx="5" cy="5" r="4.5"/><path d="M0.5 5 H9.5 M5 0.5 Q2.5 5 5 9.5 M5 0.5 Q7.5 5 5 9.5" stroke="#fff" stroke-width="0.7" fill="none"/></svg>www.brightturn.com</li>
      </ul>
    </div>
  </section>

  <section class="card card--back">
    <div class="brand"><span class="brand__dot"></span>Brightturn Wellness</div>
    <h2 class="appointment__title">Your Next Appointment is</h2>
    <p class="appointment__field appointment__field--name">Name: <span class="appointment__blank" style="width:244px"></span></p>
    <p class="appointment__field appointment__field--when">Date: <span class="appointment__blank" style="width:130px"></span>Time:<span class="appointment__blank" style="width:86px"></span></p>
    <p class="appointment__note">If unable to keep appointment,&nbsp; kindly give 24hrs notice.</p>
  </section>
</body>
</html>
```